Vellmore Family Law, legal technician needs a website and design

I need a website for a family law practice. I specialize in collaborative law, unbundled services, and mediation. The website must contain my company logo (file attached), and the website must be a mixture of my personality and my profession. I have attached additional information to explain my personality and profession.

Target Market(s)

Lower through middle-class (income level up to $200,000 per year)

Coding

Coded - Design and coding required

Number of Pages Required

1 page

Requirements
Must have
• Must have enough pages to cover required content. I submitted below some content about the collaborative law process. All of the content is not necessary. However, the website must have enough content to clearly describe the services I offer. Use your professionalism and judgment regarding font, font size, etc.

```html
<!DOCTYPE html>
<html lang="en">
<head>
<meta charset="utf-8">
<title>Vellmore Family Law</title>
<link rel="stylesheet" href="https://fonts.googleapis.com/css2?family=Cinzel:wght@600;700&family=Roboto:wght@400;500;700&display=swap">
<style>
:root{
  --navy:#0c0e3a;
  --navy-2:#1a1f5c;
  --gold:#b3a23a;
  --gold-dark:#8d7f2a;
  --grey-bg:#f3f3f3;
  --text:#6b6b6b;
  --ink:#111;
  --white:#fff;
}
*{box-sizing:border-box;margin:0;padding:0}
html,body{width:1200px;height:4922px;overflow:hidden}
body{font-family:'Roboto',Arial,sans-serif;color:var(--text);background:var(--white);position:relative}
.serif{font-family:'Cinzel',Georgia,serif}
.btn{display:inline-block;background:linear-gradient(90deg,var(--gold),var(--gold-dark));color:var(--white);font-size:14px;font-weight:700;text-transform:uppercase;padding:15px 25px;letter-spacing:.3px}
.abs{position:absolute}

/* header */
.topline{height:6px;background:var(--navy)}
.header{height:94px;position:relative}
.brand{position:absolute;left:112px;top:16px;display:flex;align-items:center;gap:12px}
.brand-mark{width:64px;height:64px;border:2px solid var(--gold)}
.brand-name{font-family:'Cinzel',Georgia,serif;font-weight:600;font-size:22px;color:var(--gold);line-height:1.1}
.brand-name small{display:block;font-size:11px;letter-spacing:1px}
.nav{position:absolute;left:397px;top:38px;display:flex;gap:22px;font-size:14px;font-weight:500;color:var(--ink)}
.nav .active{color:var(--gold)}
.phone-btn{position:absolute;left:904px;top:22px;width:184px;height:48px;border:2px solid var(--gold);display:flex;align-items:center}
.phone-btn .ic{width:46px;height:100%;display:flex;align-items:center;justify-content:center}
.phone-btn .num{flex:1;height:100%;background:var(--gold);color:#fff;font-weight:700;font-size:15px;display:flex;align-items:center;justify-content:center}

/* hero */
.hero{position:absolute;top:100px;left:0;width:1200px;height:601px;background:linear-gradient(180deg,#3f5a86 0%,#8a7a72 45%,#33302f 100%)}
.hero-box{position:absolute;left:212px;top:175px;width:746px;height:253px;background:rgba(12,14,58,.55);text-align:center;padding-top:30px}
.hero-box h1{font-family:'Cinzel',Georgia,serif;font-weight:700;font-size:27px;line-height:36px;color:#fff}
.hero-box .btn{margin-top:28px;font-size:13px;padding:14px 27px}

/* about */
.about-block{left:112px;top:800px;width:268px;height:413px;background:var(--navy)}
.about-img{left:162px;top:845px;width:433px;height:320px;background:linear-gradient(135deg,#6c7a86,#c9ccd0 60%,#3d4450);border:6px solid #fff;box-shadow:0 4px 14px rgba(0,0,0,.2)}
.play{left:347px;top:975px;width:60px;height:60px;border-radius:50%;background:var(--gold);display:flex;align-items:center;justify-content:center}
.about-text{left:648px;top:855px;width:438px}
.about-text h2{font-family:'Cinzel',Georgia,serif;font-weight:700;font-size:35px;color:var(--ink);margin-bottom:20px}
.about-text p{font-size:13px;line-height:24px;text-align:justify}
.about-text .btn{margin-top:38px}

/* services */
.svc-head{top:1300px;width:1200px;text-align:center}
.svc-head h2{font-family:'Cinzel',Georgia,serif;font-weight:700;font-size:35px;color:var(--ink)}
.svc-head p{font-size:14px;line-height:24px;margin-top:20px}
.svc-row{left:0;width:1200px;height:446px;background:var(--grey-bg)}
.svc-img{position:absolute;top:0;width:600px;height:446px}
.svc-text{position:absolute;top:52px;width:395px}
.svc-text h3{font-family:'Cinzel',Georgia,serif;font-weight:700;font-size:25px;color:var(--ink);margin-bottom:22px}
.svc-text p{font-size:13px;line-height:24px;text-align:justify;margin-bottom:14px}
.svc-text .btn{margin-top:24px}
.svc-icon{position:absolute;left:558px;top:179px;width:84px;height:84px;border-radius:50%;background:var(--navy);border:5px solid #fff;display:flex;align-items:center;justify-content:center}

/* testimonials */
.testi{top:2782px;left:0;width:1200px;height:460px;background:linear-gradient(90deg,#0c0e3a,#1b2160 50%,#0c0e3a);text-align:center;color:#fff}
.testi h2{font-family:'Cinzel',Georgia,serif;font-weight:700;font-size:35px;margin-top:48px}
.quote-ic{width:54px;height:54px;border-radius:50%;background:var(--gold);margin:30px auto 0;display:flex;align-items:center;justify-content:center}
.testi p{width:810px;margin:34px auto 0;font-size:13px;line-height:26px;color:#e6e6ee}
.stars{margin-top:14px;color:var(--gold);font-size:16px;letter-spacing:2px}
.who{margin-top:8px;font-weight:700;font-size:19px}
.who span{font-weight:400;font-size:14px}
.dots{display:flex;justify-content:center;gap:10px;margin-top:34px}
.dots i{width:14px;height:14px;border-radius:50%;border:1px solid #fff;display:block}
.dots i.on{width:22px;height:22px;margin-top:-4px;border:2px solid #fff;background:radial-gradient(var(--gold) 45%,transparent 50%)}
.arrow{top:3005px}

/* blog */
.blog-head{top:3320px;width:1200px;text-align:center;font-family:'Cinzel',Georgia,serif;font-weight:700;font-size:39px;color:var(--ink)}
.card{top:3421px;width:316px;height:434px}
.card-img{height:247px;background:linear-gradient(135deg,#8c8a86,#d8d6d1 55%,#55585c)}
.card-body{position:absolute;left:16px;top:230px;width:300px;height:204px;background:#fff;box-shadow:0 2px 10px rgba(0,0,0,.15);padding:16px 28px}
.card-date{font-size:13px;color:#333;display:flex;align-items:center;gap:8px}
.card h4{font-size:18px;line-height:25px;color:var(--ink);margin-top:12px;font-weight:700}
.card p{font-size:12px;line-height:21px;margin-top:10px;text-align:justify}
.card .more{font-size:13px;color:var(--gold);font-weight:700;margin-top:10px}

/* cta */
.cta{top:3950px;left:0;width:1200px;height:570px;background:linear-gradient(90deg,#121420,#2a2c33 50%,#14161f)}
.cta h2{font-family:'Cinzel',Georgia,serif;font-weight:700;font-size:29px;line-height:37px;color:#fff;text-align:center;margin-top:42px}
.contact-item{position:absolute;top:175px;display:flex;align-items:center;gap:16px}
.contact-item .c{width:40px;height:40px;border-radius:50%;background:var(--gold);display:flex;align-items:center;justify-content:center}
.contact-item .l{font-size:15px;color:var(--gold)}
.contact-item .v{font-size:15px;color:#fff}
.quote-btn{position:absolute;left:798px;top:174px;font-size:13px;padding:14px 16px}
.form{top:4215px;left:232px;width:736px;height:385px;background:#fff;border-left:6px solid var(--gold);border-right:6px solid var(--gold);text-align:center;padding-top:30px}
.form h3{font-family:'Cinzel',Georgia,serif;font-weight:700;font-size:29px;color:var(--ink)}
.fields{width:590px;margin:28px auto 0;display:grid;grid-template-columns:1fr 1fr;gap:10px}
.field{height:48px;border:1px solid #ccc;font-size:14px;color:#666;text-align:left;padding:14px 12px}
.field.wide{grid-column:1/3;height:110px}
.send{grid-column:1/3;margin-top:4px;height:46px;background:linear-gradient(90deg,var(--gold),var(--gold-dark));color:#fff;font-size:14px;font-weight:700;display:flex;align-items:center;justify-content:center}

/* footer */
.footer{top:4520px;left:0;width:1200px;height:402px;background:var(--navy);color:#fff}
.footer .brand{top:135px}
.socials{position:absolute;left:130px;top:248px;display:flex;gap:8px}
.socials i{display:block;width:34px;height:34px;border-radius:50%;background:var(--gold)}
.socials i:nth-child(2),.socials i:nth-child(4){background:#fff}
.fcol{position:absolute;top:135px}
.fcol h5{font-size:19px;font-weight:500;margin-bottom:22px}
.fcol li{list-style:none;font-size:14px;line-height:26px;display:flex;gap:16px;align-items:flex-start}
.fcol li b{color:var(--gold);font-weight:700}
.copyright{position:absolute;left:112px;top:356px;width:976px;border-top:1px solid #2e3160;padding-top:16px;text-align:center;font-size:12px}
.chat{position:absolute;left:1118px;top:290px;width:44px;height:44px;border-radius:50%;background:var(--gold)}
</style>
</head>
<body>
<div class="topline"></div>
<header class="header">
  <div class="brand"><span class="brand-mark"></span><span class="brand-name">Vellmore<small>Family Law</small></span></div>
  <nav class="nav"><span class="active">HOME</span><span>ABOUT US</span><span>OUR SERVICES</span><span>BLOG</span><span>CONTACT US</span></nav>
  <div class="phone-btn"><span class="ic"><svg width="18" height="18" viewBox="0 0 24 24" fill="#b3a23a"><path d="M6.6 10.8a15 15 0 006.6 6.6l2.2-2.2c.3-.3.7-.4 1-.2 1.1.4 2.3.6 3.6.6.6 0 1 .4 1 1V20c0 .6-.4 1-1 1A17 17 0 013 4c0-.6.4-1 1-1h3.5c.6 0 1 .4 1 1 0 1.3.2 2.5.6 3.6.1.3 0 .7-.2 1z"/></svg></span><span class="num">123-456-7890</span></div>
</header>

<section class="hero" role="img" aria-label="City skyline with observation tower at dusk">
  <div class="hero-box">
    <h1>Vellmore Family Law, Collaborative Law and<br>Unbundled Legal Services in King<br>County, Washington State.</h1>
    <span class="btn">Get Started</span>
  </div>
</section>

<div class="abs about-block"></div>
<div class="abs about-img" role="img" aria-label="Smiling lawyer talking with a client"></div>
<div class="abs play"><svg width="20" height="20" viewBox="0 0 20 20"><path d="M5 3l12 7-12 7z" fill="#fff"/></svg></div>
<div class="abs about-text">
  <h2>About Us</h2>
  <p>Lorem ipsum dolor sit amet, consectetur adipiscing elit, sed do eiusmod tempor incididunt ut labore et dolore magna aliqua. Ut enim ad minim veniam, quis nostrud exercitation ullamco laboris nisi ut aliquip ex ea commodo consequat. Duis aute irure dolor in reprehenderit in voluptate velit esse cillum dolore eu fugiat nulla pariatur. excepteur sint occaec t labore et dolorat.</p>
  <span class="btn">Learn More</span>
</div>

<div class="abs svc-head">
  <h2>Our Services</h2>
  <p>Lorem ipsum dolor sit amet, consectetur adipiscing elit, sed do eiusmod tempor incididunt ut<br>labore et or sit am dolodpvesm quis nostrud.</p>
</div>

<section class="abs svc-row" style="top:1446px">
  <div class="svc-text" style="left:112px"><h3>Collaborative Law</h3>
    <p>Collaborate practice is a process where trained professionals, including attorneys, help couples resolve their disputes without litigation and outside of court. Instead, those involved in the case approach the legal process through the lens of teamwork, trouble-shooting, and problem-solving rather than fighting to “beat” someone else.</p>
    <p>Another way of describing this process is rather than looking at a “win – lose” result, see it as a “win-win” for all involved.</p>
    <span class="btn">Learn More</span></div>
  <div class="svc-img" style="left:600px;background:linear-gradient(135deg,#c7c9cc,#f2f0ec 55%,#8a7d6c)" role="img" aria-label="Team meeting around a table with documents"></div>
  <div class="svc-icon"><svg width="40" height="40" viewBox="0 0 40 40" fill="none" stroke="#fff" stroke-width="2"><path d="M20 6v24M10 12h20M10 12l-5 10h10zM30 12l-5 10h10zM12 34h16"/></svg></div>
</section>

<section class="abs svc-row" style="top:1892px">
  <div class="svc-img" style="left:0;background:linear-gradient(135deg,#e6e7e9,#c5c0b8 50%,#4e5260)" role="img" aria-label="Lawyer reviewing a document with a client"></div>
  <div class="svc-text" style="left:693px"><h3>Unbundled Services</h3>
    <p>Lawyer and client contract for specific and limited legal services without the lawyer being responsible for the whole case, i.e. a parenting plan.</p>
    <p>Lorem ipsum dolor sit amet, consectetur adipiscing elit, sed do eiusmod tempor incididunt ut labore et dolore magna aliqua. Ut enim ad minim veniam, quis nostrud exercitation ullamco laboris nisi ut aliquip ex ea commodo consequat. Duis ar incididunt ut labored minim veniam, quis ute .</p>
    <span class="btn">Learn More</span></div>
  <div class="svc-icon"><svg width="40" height="40" viewBox="0 0 40 40" fill="none" stroke="#fff" stroke-width="2"><rect x="10" y="6" width="20" height="28"/><path d="M14 13h12M14 18h12M14 23h8"/></svg></div>
</section>

<section class="abs svc-row" style="top:2337px">
  <div class="svc-text" style="left:112px"><h3>Mediation</h3>
    <p>Mediation can be highly constructive for couples and families seeking to resolve their disputes and plan for the future without litigation. With a mediator facilitating the process, clients work through the financial problems and the parenting questions at the pace and in the manner with which they feel most comfortable.</p>
    <p>They are the ones who drive the process and who determine their own solutions, albeit with guidance</p>
    <span class="btn">Learn More</span></div>
  <div class="svc-img" style="left:600px;background:linear-gradient(135deg,#5a4a3e,#a8876a 50%,#3c3a40)" role="img" aria-label="Couple meeting with a mediator holding a clipboard"></div>
  <div class="svc-icon"><svg width="40" height="40" viewBox="0 0 40 40" fill="none" stroke="#fff" stroke-width="2"><circle cx="20" cy="12" r="4"/><path d="M12 24h16v8H12zM8 34h24"/></svg></div>
</section>

<section class="abs testi">
  <h2>What Our Clients Say</h2>
  <div class="quote-ic"><svg width="24" height="20" viewBox="0 0 24 20" fill="#fff"><path d="M0 10h6l-3 8h4l3-8V2H0zM14 10h6l-3 8h4l3-8V2h-10z"/></svg></div>
  <p>Lorem ipsum dolor sit amet, consectetur adipiscing elit, sed do eiusmod tempor incididunt ut labore et dolore magna aliqua. Ut enim ad minim veniam, quis nostrud exercitation ullamco laboris nisi ut aliquip ex ea commodo consequat. Duis aute irure dolor in reprehenderit in voluptate velit esse cillum dolore eu fugiat nulla pariatur.</p>
  <div class="stars">★★★★★</div>
  <div class="who">OLIVIA MARSH, <span>Washington</span></div>
  <div class="dots"><i></i><i class="on"></i><i></i><i></i><i></i></div>
</section>
<svg class="abs arrow" style="left:96px" width="18" height="26" viewBox="0 0 18 26"><path d="M14 3L4 13l10 10" stroke="#fff" stroke-width="3" fill="none"/></svg>
<svg class="abs arrow" style="left:1084px" width="18" height="26" viewBox="0 0 18 26"><path d="M4 3l10 10L4 23" stroke="#fff" stroke-width="3" fill="none"/></svg>

<h2 class="abs blog-head">Latest Blog &amp; Articles</h2>
<article class="abs card" style="left:112px"><div class="card-img" role="img" aria-label="Smiling businesswoman shaking hands"></div>
  <div class="card-body"><div class="card-date"><svg width="14" height="14" viewBox="0 0 14 14" fill="#b3a23a"><rect x="1" y="3" width="12" height="10"/><rect x="1" y="1" width="12" height="3" fill="#8d7f2a"/></svg>18 JUN 2021</div><h4>Lorem ipsum dolor sit amet, consectetur adi</h4><p>Sed ut perspiciatis unde omnis iste nat us error sit voluptatem accusantium dol oremque laudantium, totam.</p><div class="more">Read More &nbsp;➜</div></div></article>
<article class="abs card" style="left:442px"><div class="card-img" role="img" aria-label="Handshake over a desk with a gavel"></div>
  <div class="card-body"><div class="card-date"><svg width="14" height="14" viewBox="0 0 14 14" fill="#b3a23a"><rect x="1" y="3" width="12" height="10"/><rect x="1" y="1" width="12" height="3" fill="#8d7f2a"/></svg>18 JUN 2021</div><h4>Lorem ipsum dolor sit amet, consectetur adi</h4><p>Sed ut perspiciatis unde omnis iste nat us error sit voluptatem accusantium dol oremque laudantium, totam.</p><div class="more">Read More &nbsp;➜</div></div></article>
<article class="abs card" style="left:772px"><div class="card-img" role="img" aria-label="Two women signing papers at an office desk"></div>
  <div class="card-body"><div class="card-date"><svg width="14" height="14" viewBox="0 0 14 14" fill="#b3a23a"><rect x="1" y="3" width="12" height="10"/><rect x="1" y="1" width="12" height="3" fill="#8d7f2a"/></svg>18 JUN 2021</div><h4>Lorem ipsum dolor sit amet, consectetur adi</h4><p>Sed ut perspiciatis unde omnis iste nat us error sit voluptatem accusantium dol oremque laudantium, totam.</p><div class="more">Read More &nbsp;➜</div></div></article>

<section class="abs cta" role="img" aria-label="Dark background of a handshake at a desk">
  <h2>Vellmore Family Law, Collaborative Law and<br>Unbundled Legal Services in King<br>County, Washington State.</h2>
  <div class="contact-item" style="left:232px"><span class="c"><svg width="16" height="16" viewBox="0 0 24 24" fill="#fff"><path d="M6.6 10.8a15 15 0 006.6 6.6l2.2-2.2c.3-.3.7-.4 1-.2 1.1.4 2.3.6 3.6.6.6 0 1 .4 1 1V20c0 .6-.4 1-1 1A17 17 0 013 4c0-.6.4-1 1-1h3.5c.6 0 1 .4 1 1 0 1.3.2 2.5.6 3.6.1.3 0 .7-.2 1z"/></svg></span><div><div class="l">Call Me</div><div class="v">123-456-7890</div></div></div>
  <div class="contact-item" style="left:497px"><span class="c"><svg width="16" height="14" viewBox="0 0 16 14" fill="none" stroke="#fff" stroke-width="1.6"><rect x="1" y="1" width="14" height="12"/><path d="M1 1l7 6 7-6"/></svg></span><div><div class="l">Email Me</div><div class="v">info@vellmore.com</div></div></div>
  <span class="btn quote-btn">Get A Free Quote</span>
</section>

<footer class="abs footer">
  <div class="brand"><span class="brand-mark"></span><span class="brand-name">Vellmore<small>Family Law</small></span></div>
  <div class="socials"><i></i><i></i><i></i><i></i></div>
  <div class="fcol" style="left:405px"><h5>Quick Links</h5><ul><li><b>➜</b>Home</li><li><b>➜</b>About Us</li><li><b>➜</b>Our Services</li><li><b>➜</b>Blog</li><li><b>➜</b>Contact Us</li></ul></div>
  <div class="fcol" style="left:620px"><h5>Our Services</h5><ul><li><b>➜</b>Collaborative Law</li><li><b>➜</b>Unbundled Services</li><li><b>➜</b>Mediation</li></ul></div>
  <div class="fcol" style="left:900px"><h5>Contact Us</h5><ul><li><b>●</b>456, Washington State,<br>United States</li><li><b>☎</b>123-456-7890</li><li><b>▣</b>123-456-7890</li><li><b>✉</b>info@vellmore.com</li></ul></div>
  <div class="chat"></div>
  <div class="copyright">© Copyrights 2021 Company Name. All Rights Reserved &nbsp; | &nbsp; Privacy Policy &nbsp; | &nbsp; Terms Of Use</div>
</footer>

<div class="abs form">
  <h3>Request A Free Quote</h3>
  <div class="fields">
    <div class="field">First Name</div><div class="field">Last Name</div>
    <div class="field">Email Address</div><div class="field">Phone Number</div>
    <div class="field wide">Message....</div>
    <div class="send">CONTACT NOW</div>
  </div>
</div>
</body>
</html>
```